Brindleworth.com -> We need someone to design a homepage [For Mobile]

We need a graphic design of our homepage for mobile, which will include login and signup. It's only the design we need, we would take care of the coding, so if you're a good designer you're welcome to participate. The Login & Registration page contain a few fields. Login --> Username & Password & Forgot my Password. Registration --> Email, Username, Password. Needs to be a clean design.[Registration in a different page, Login and Homepage in the same one]
Updates

Project Deadline Extended Reason: We're going to consider what we got so far and allow others to submit more designs as well, the final deadline would be this week, we won't extend it again. Added Saturday, December 20, 2014

Project Deadline Extended Reason: Very sorry, we just got more than expected designs and we want to go over all of them in order to make a proper decision - we would extend the project until the 1st of January 2015, this is definitely a FINAL date. Added Friday, December 26, 2014

Industry/Entity Type

Graphic Design

Number of Pages Required

2 page

Requirements
Must have
• * Enclosed our logo to include with the design.
• * Add the following text as well
• WANT TO EARN EXTRA MONEY?
• WITH BRINDLEWORTH.COM YOU CAN!
• BRINDLEWORTH.COM. IT'S AS EASY AS 1, 2, 3.
• (1) Register (2) Earn & Win Coins (3) Redeem Coins
• * It must have "Login" and "Register" buttons on the home page.
Nice to have
• [Note: Also to make it easier for you, enclosed a screenshot of the main page in a desktop (PC) view.]

```html
<!DOCTYPE html>
<html lang="en">
<head>
<meta charset="utf-8">
<title>Brindleworth.com – Mobile Home</title>
<link href="https://fonts.googleapis.com/css2?family=Roboto:wght@400;500;700&display=swap" rel="stylesheet">
<style>
:root{
  --page-bg:#4fa84c;
  --white:#ffffff;
  --ink:#3a4149;
  --slate:#34495a;
  --green:#3f9a2a;
  --green-dark:#2f7f1f;
  --green-bright:#8fe03a;
  --band-green:#338a22;
  --grey-bg:#d9d9d9;
  --btn-grey:#ececec;
  --btn-border:#c4c4c4;
  --rule:#d3d3d3;
  --footer:#b4c2c6;
  --step1:#e9b71f;
  --step2:#d9411a;
  --step3:#4a8f1c;
  --hero-top:#6e5a3e;
  --hero-mid:#5a4a33;
  --hero-low:#8a4a26;
}
*{margin:0;padding:0;box-sizing:border-box}
html,body{width:823px;height:1200px;overflow:hidden}
body{background:var(--page-bg);font-family:"Roboto",Arial,sans-serif;color:var(--ink)}
.screen{position:absolute;left:84px;top:3px;width:654px;height:1194px;background:var(--grey-bg);overflow:hidden}
.abs{position:absolute}

.site-header{left:0;top:0;width:654px;height:118px;background:linear-gradient(#ffffff 55%,#eeeeee)}
.brand{left:24px;top:34px;display:flex;align-items:center;gap:12px}
.brand-dot{width:48px;height:48px;border-radius:50%;background:var(--slate)}
.brand-name{font-size:30px;font-weight:500;color:var(--slate);white-space:nowrap}
.header-actions{left:370px;top:43px;display:flex;gap:8px}
.header-button{height:32px;padding:0 12px;display:flex;align-items:center;justify-content:center;font-size:14px;font-weight:700;white-space:nowrap;border-radius:2px}
.login-button{border:2px solid var(--green);color:var(--green);background:var(--white)}
.register-button{background:var(--green);color:var(--white);border:2px solid var(--green)}
.menu-toggle{left:563px;top:44px;width:62px;height:30px}

.hero{left:0;top:118px;width:654px;height:339px;background:linear-gradient(180deg,var(--hero-top),var(--hero-mid) 60%,var(--hero-low))}
.hero-copy{left:0;width:654px;text-align:center;color:var(--white);font-weight:700;text-shadow:0 2px 3px rgba(0,0,0,.5);white-space:nowrap}
.hero-title{top:176px;font-size:33px;color:var(--green-bright)}
.hero-sub{top:218px;font-size:24px;line-height:30px;font-weight:500}
.email-field{left:156px;top:303px;width:342px;height:47px;border-radius:24px;background:var(--white);border:3px solid #2b2b2b;display:flex;align-items:center;justify-content:center;font-size:13px;color:#666}
.join-button{left:222px;top:364px;width:210px;height:46px;background:var(--green);color:var(--white);font-size:16px;font-weight:700;display:flex;align-items:center;justify-content:center;text-align:center;white-space:nowrap;border-radius:2px}
.hero-arrow{top:274px;width:20px;height:28px}

.green-band{left:0;top:457px;width:654px;height:273px;background:var(--band-green)}
.card{left:18px;top:468px;width:617px;height:648px;background:var(--white)}
.card-title{left:0;top:502px;width:654px;text-align:center;font-size:26px;font-weight:700;color:var(--ink);white-space:nowrap}
.step-line{left:96px;top:593px;width:442px;height:4px;background:var(--green)}
.step-dot{width:54px;height:54px;border-radius:50%;top:568px;border:3px solid rgba(255,255,255,.6);color:var(--white);font-weight:700;font-size:20px;display:flex;align-items:center;justify-content:center;box-shadow:0 0 0 1px rgba(0,0,0,.15)}
.step-label{top:630px;width:200px;text-align:center;font-size:21px;font-weight:500;color:var(--ink);letter-spacing:.3px;white-space:nowrap}
.rule{left:55px;width:556px;height:2px;background:var(--rule)}
.feed-button{left:92px;width:469px;height:63px;background:var(--btn-grey);border:2px solid var(--btn-border);display:flex;align-items:center;justify-content:center;gap:16px;font-size:27px;font-weight:700;color:var(--green);white-space:nowrap}
.stat-amount{left:0;top:880px;width:654px;text-align:center;font-size:38px;font-weight:700;color:var(--slate)}
.stat-caption{left:0;top:929px;width:654px;text-align:center;font-size:20px;font-weight:700;color:var(--green-dark);white-space:nowrap}
.partners-title{left:0;top:1003px;width:654px;text-align:center;font-size:20px;font-weight:500;color:var(--slate)}
.partner-badge{background:#f1f1f1;border:2px solid #8e8e8e}
.site-footer{left:18px;top:1116px;width:617px;height:78px;background:var(--footer);display:flex;align-items:center;justify-content:center;font-size:14px;color:var(--ink)}
</style>
</head>
<body>
<main class="screen">
  <header class="site-header abs">
    <div class="brand abs"><span class="brand-dot"></span><span class="brand-name">brindleworth</span></div>
    <nav class="header-actions abs">
      <span class="header-button login-button">LOGIN</span>
      <span class="header-button register-button">REGISTER</span>
    </nav>
    <svg class="menu-toggle abs" viewBox="0 0 62 30" aria-label="Menu"><rect y="0" width="62" height="5" fill="#34495a"/><rect y="12" width="62" height="5" fill="#34495a"/><rect y="24" width="62" height="5" fill="#34495a"/></svg>
  </header>

  <section class="hero abs" role="img" aria-label="Illustrated landscape with palm trees, clouds and a hill at sunset"></section>
  <h1 class="hero-copy hero-title abs">WANT TO EARN EXTRA MONEY?</h1>
  <p class="hero-copy hero-sub abs">WITH BRINDLEWORTH.COM YOU CAN!<br>BRINDLEWORTH.COM. IT'S AS EASY AS 1, 2, 3.</p>
  <div class="email-field abs">Enter Email</div>
  <div class="join-button abs">JOIN BRINDLEWORTH</div>
  <svg class="hero-arrow abs" style="left:16px" viewBox="0 0 20 28"><path d="M15 3 L5 14 L15 25" fill="none" stroke="#fff" stroke-width="2.5"/></svg>
  <svg class="hero-arrow abs" style="left:618px" viewBox="0 0 20 28"><path d="M5 3 L15 14 L5 25" fill="none" stroke="#fff" stroke-width="2.5"/></svg>

  <div class="green-band abs"></div>
  <section class="card abs"></section>
  <h2 class="card-title abs">BRINDLEWORTH.COM. IT'S AS EASY AS 1, 2, 3.</h2>
  <div class="step-line abs"></div>
  <div class="step-dot abs" style="left:69px;background:var(--step1)">1</div>
  <div class="step-dot abs" style="left:290px;background:var(--step2)">2</div>
  <div class="step-dot abs" style="left:511px;background:var(--step3)">3</div>
  <div class="step-label abs" style="left:-4px">Register</div>
  <div class="step-label abs" style="left:217px">Earn &amp; Win Coins</div>
  <div class="step-label abs" style="left:438px">Redeem Coins</div>
  <div class="rule abs" style="top:695px"></div>

  <div class="feed-button abs" style="top:723px">
    <svg width="48" height="40" viewBox="0 0 48 40" aria-hidden="true"><circle cx="30" cy="10" r="8" fill="#7b7b7b"/><path d="M16 38c0-10 6-16 14-16s14 6 14 16z" fill="#7b7b7b"/><circle cx="16" cy="12" r="8" fill="#9a9a9a"/><path d="M2 38c0-10 6-16 14-16s14 6 14 16z" fill="#9a9a9a"/></svg>
    RECENT MEMBER ACTIVITY
  </div>
  <div class="feed-button abs" style="top:804px">
    <svg width="42" height="42" viewBox="0 0 42 42" aria-hidden="true"><circle cx="21" cy="21" r="20" fill="#6d6d6d"/><text x="21" y="30" text-anchor="middle" font-family="Roboto,Arial,sans-serif" font-size="26" font-weight="700" fill="#fff">$</text></svg>
    RECENTLY REDEEMED
  </div>

  <div class="stat-amount abs">OVER $250,000</div>
  <div class="stat-caption abs">HAS BEEN CLAIMED BY OUR MEMBERS IN THE STORE</div>
  <div class="rule abs" style="top:979px"></div>

  <div class="partners-title abs">OUR PARTNERS</div>
  <div class="partner-badge abs" style="left:37px;width:164px;top:1052px;height:32px" aria-label="Rewardly partner badge"></div>
  <div class="partner-badge abs" style="left:218px;width:201px;top:1049px;height:40px" aria-label="TaskHarbor partner badge"></div>
  <div class="partner-badge abs" style="left:439px;width:166px;top:1047px;height:44px" aria-label="Sonicbay partner badge"></div>

  <footer class="site-footer abs">Copyright © 2014.BRINDLEWORTH. All Right Reserved</footer>
</main>
</body>
</html>
```